Lantern Petals Website v.1 - attract floral shop franchisees

I need a simple information website for my new business. We are a franchisor of flower shops. The overall purpose of the website is to promote the company and the service, especially to potential franchisees and retailers. Only about 4 pages are required including homepage, About, For Supermarkets, For Franchisees, and Contact. No special functions are required except the site will have two separate inquiry forms that must be filled out online and submitted via automated email. Similarly, an email form should be linked from the Contact page. I have a logo and business cards designed by ArtMingle, and I would like the site to have a consistent color scheme and style. The key to design will be to express the joy and love associated with flowers and floral bouquets.
IMPORTANT - I will be exporting the website design to Wordpress CMS in a site hosted by HostNimbus. For smooth integration into WordPress hosted by HostNimbus, the designer should build the site using a WordPress-friendly format. Ideally, they should use HTML, CSS, and PHP. Creating a custom theme or using a page builder that exports to WordPress-compatible files is best. This ensures the site can be easily imported and managed within WordPress.

Target Market(s)

Potential franchisees (existing florists or creative types who might like to own a floral business) and supermarkets who might want us to run their floral department

Industry/Entity Type

Floral retailing

Requirements
Must have
• A brand theme that is beautiful, consistent throughout and builds on the logo design
Nice to have
• Show gender and ethnic diversity in customers and florists. Pictures of happy florists (for franchisees) and pictures of amazing floral department displays (for supermarkets)

```html
<!DOCTYPE html>
<html lang="en">
<head>
<meta charset="utf-8">
<title>Lantern Petals – Floral Franchising</title>
<link href="https://fonts.googleapis.com/css2?family=Josefin+Sans:wght@300;400;500;600&family=Great+Vibes&display=swap" rel="stylesheet">
<style>
  :root{
    --mint:#e2fcef;
    --orange:#f1ad2c;
    --nav:#e0a023;
    --green:#13924a;
    --ink:#2e2e2e;
    --white:#ffffff;
  }
  *{box-sizing:border-box;margin:0;padding:0}
  html,body{width:1200px;height:3236px;overflow:hidden}
  body{position:relative;background:var(--white);font-family:'Josefin Sans',sans-serif;color:var(--ink)}
  .abs{position:absolute}
  .script{font-family:'Great Vibes',cursive;font-weight:400}
  .btn{position:absolute;display:flex;align-items:center;justify-content:center;border-radius:24px;background:var(--green);color:var(--white);font-weight:500;font-size:17px;letter-spacing:.3px;text-transform:uppercase;box-shadow:0 3px 6px rgba(0,0,0,.18);padding-top:3px;white-space:nowrap}
  .ph{position:absolute}

  /* header + hero */
  .hero-bg{left:0;top:0;width:1200px;height:680px;background:var(--mint)}
  .brand{display:flex;align-items:center;gap:14px;color:var(--orange);font-weight:500;font-size:34px;letter-spacing:1px;white-space:nowrap}
  .brand-dot{width:46px;height:46px;border-radius:50%;background:var(--orange)}
  .call{left:719px;top:12px;display:flex;align-items:center;gap:12px}
  .call-icon{width:46px;height:46px;border-radius:50%;border:2px solid var(--orange);display:flex;align-items:center;justify-content:center}
  .call-label{color:var(--orange);font-size:16px;font-weight:500;letter-spacing:.5px}
  .call-num{font-size:16px;margin-top:4px}
  .login{left:961px;top:12px;width:126px;height:43px;font-size:17px}
  .nav{left:410px;top:69px;width:790px;height:63px;background:var(--nav)}
  .nav-home{position:absolute;left:0;top:0;width:106px;height:63px;background:var(--green);clip-path:polygon(30px 0,100% 0,100% 100%,0 100%)}
  .nav ul{position:absolute;left:40px;top:0;height:63px;display:flex;align-items:center;list-style:none;gap:29px;color:var(--white);font-size:15.5px;letter-spacing:.3px;padding-top:4px;white-space:nowrap}
  .hero-title{left:111px;top:215px;color:var(--orange);font-size:92px;font-weight:500;line-height:1;letter-spacing:3px}
  .hero-sub{left:111px;top:352px;color:var(--green);font-size:46px;font-weight:500;letter-spacing:30px}
  .get-started{left:111px;top:412px;width:155px;height:47px}

  /* about */
  .sec-title{font-size:66px;line-height:1;white-space:nowrap}
  .copy{font-size:17.5px;line-height:28.4px;font-weight:300}

  /* supermarkets */
  .market{left:0;top:1171px;width:1200px;height:682px;background:linear-gradient(90deg,#2a150d 0%,#4a2a1a 35%,#8a6a58 55%,#b99e8e 75%,#4e6770 100%)}
  .market-text{color:var(--white)}
  .bullet{font-size:17.5px;line-height:25px;font-weight:300;color:var(--white);white-space:nowrap}
  .bullet b{color:var(--orange);font-weight:600;margin-right:4px}

  /* cta */
  .cta-head{left:328px;top:2513px;color:#1d2a2a;font-size:31.5px;line-height:42px;font-weight:500;letter-spacing:.6px;text-transform:uppercase;white-space:nowrap}
  .btn-outline{background:transparent;border:2px solid var(--white);color:#1d2a2a;box-shadow:0 3px 6px rgba(0,0,0,.12)}

  /* footer */
  .foot-title{font-size:36px;color:var(--green);white-space:nowrap}
  .foot-link{font-size:17px;letter-spacing:.4px;white-space:nowrap}
  .contact-row{display:flex;align-items:flex-start;gap:16px;white-space:nowrap}
  .c-icon{width:42px;height:42px;border-radius:50%;background:var(--green);display:flex;align-items:center;justify-content:center;flex:none}
  .c-label{font-size:20px;font-weight:500}
  .c-val{font-size:16.5px;margin-top:2px}
  .copyright{left:0;top:3187px;width:1200px;text-align:center;font-size:15px;font-weight:300}
</style>
</head>
<body>

<!-- HERO -->
<div class="abs hero-bg"></div>

<div class="abs brand" style="left:110px;top:48px">
  <span class="brand-dot"></span><span>Lantern Petals</span>
</div>

<div class="abs call">
  <div class="call-icon">
    <svg width="20" height="20" viewBox="0 0 24 24"><path fill="#f1ad2c" d="M6.6 10.8a15 15 0 0 0 6.6 6.6l2.2-2.2c.3-.3.7-.4 1-.2 1.1.4 2.3.6 3.6.6.6 0 1 .4 1 1V20c0 .6-.4 1-1 1A17 17 0 0 1 3 4c0-.6.4-1 1-1h3.5c.6 0 1 .4 1 1 0 1.3.2 2.5.6 3.6.1.3 0 .7-.2 1z"/></svg>
  </div>
  <div>
    <div class="call-label">CALL US :</div>
    <div class="call-num">+1 555 204 7781</div>
  </div>
</div>
<div class="btn login">LOGIN</div>

<nav class="abs nav">
  <div class="nav-home"></div>
  <ul>
    <li>HOME</li>
    <li>ABOUT US</li>
    <li>FOR SUPERMARKETS</li>
    <li>FOR FRANCHISEES</li>
    <li>CONTACT US</li>
  </ul>
</nav>

<div class="abs hero-title">Lantern</div>
<div class="abs hero-sub">PETALS</div>
<div class="btn get-started">GET STARTED</div>

<div class="ph" role="img" aria-label="Bouquet of pink roses and white flowers wrapped in lace, framed by an orange circle" style="left:660px;top:150px;width:420px;height:470px;border-radius:48% 48% 40% 40%;background:radial-gradient(circle at 50% 40%,#f6c4b8 0%,#eab2a2 35%,#9fb48c 65%,#e2fcef 100%)"></div>

<svg class="abs" style="left:0;top:520px" width="1200" height="180" viewBox="0 0 1200 180">
  <path d="M0 140 C140 40 330 10 560 60 C760 105 900 120 1050 70 C1120 45 1170 25 1200 14 L1200 180 L0 180 Z" fill="#f1ad2c"/>
  <path d="M0 180 C150 100 340 75 560 105 C760 135 900 135 1040 90 C1110 66 1165 35 1200 14 L1200 180 Z" fill="#ffffff"/>
</svg>

<!-- ABOUT -->
<div class="ph" role="img" aria-label="Smiling woman in a straw hat holding a colourful bouquet, inside an orange circle with a green rim" style="left:119px;top:716px;width:387px;height:361px;border-radius:50%;background:radial-gradient(circle at 55% 45%,#f7d9c6 0%,#f1ad2c 55%,#f1ad2c 96%,#13924a 97%)"></div>

<div class="abs script sec-title" style="left:592px;top:762px;color:var(--green)">About <span style="color:var(--orange)">Us</span></div>
<p class="abs copy" style="left:592px;top:848px;width:510px">Fresh flowers convey beauty and love, and in our view should become something every person regularly enjoys.  Lantern Petals is an entrepreneurial company created to make top quality fresh flowers and professionally-designed bouquets accessible to every consumer at affordable prices.</p>
<div class="btn" style="left:592px;top:999px;width:138px;height:44px">READ MORE</div>

<!-- SUPERMARKETS -->
<div class="ph market" role="img" aria-label="Smiling woman holding a large bouquet of daisies, sunflowers and lilies in a shop, darkened on the left"></div>
<div class="abs script sec-title market-text" style="left:111px;top:1282px">For Supermarkets</div>
<p class="abs copy market-text" style="left:111px;top:1363px;width:480px">Lantern Petals works with some of the country’s largest and most progressive supermarkets to provide franchisee ownership and operation of their strategically important floral departments.  Supermarkets find that Lantern Petals is able to improve their financial outcomes, provide attentive customer service and satisfaction, and lift the quality of the entire store environment.</p>
<div class="abs" style="left:111px;top:1594px;color:var(--white);font-size:18.5px;font-weight:600;letter-spacing:.3px;white-space:nowrap">Opportunity For Supermarkets</div>
<div class="abs bullet" style="left:111px;top:1636px"><b>»</b>Enhance floral revenue streams with efficient<br><span style="padding-left:18px">assortments and new offerings</span></div>
<div class="abs bullet" style="left:111px;top:1695px"><b>»</b>Reduce the costs of operating a floral department</div>
<div class="btn" style="left:113px;top:1734px;width:140px;height:45px">READ MORE</div>

<!-- FRANCHISEES -->
<div class="abs script sec-title" style="left:111px;top:1985px;color:var(--green)">For <span style="color:var(--orange)">Franchisees</span></div>
<p class="abs" style="left:111px;top:2076px;width:530px;font-size:20px;line-height:31px;font-weight:300">Lantern Petals brings the best of professional florists and supermarkets together for the benefit of consumers.  It supports a national network of owner-operator franchisees, who in many cases are multi-site professional florists, with comprehensive services to enhance franchise profitability.</p>
<div class="btn" style="left:110px;top:2240px;width:140px;height:47px">READ MORE</div>

<div class="ph" role="img" aria-label="Bouquet of pink roses and gerbera daisies inside a circle with a green rim" style="left:691px;top:1944px;width:352px;height:359px;border-radius:50%;background:radial-gradient(circle at 45% 45%,#f59ab0 0%,#e0507e 40%,#c88a7a 75%,#c88a7a 95%,#13924a 96%)"></div>

<!-- CTA -->
<svg class="abs" style="left:0;top:2431px" width="1200" height="440" viewBox="0 0 1200 440">
  <path d="M0 0 L1200 0 L1200 322 C1100 380 950 404 790 398 C600 390 420 370 250 372 C140 374 50 385 0 405 Z" fill="#f1ad2c"/>
  <path d="M0 405 C50 385 140 374 250 372 C420 370 600 390 790 398 C950 404 1100 380 1200 322 L1200 440 L0 440 Z" fill="#e2fcef"/>
</svg>
<div class="ph" role="img" aria-label="Smiling woman in a white dress holding a bouquet of pink and white peonies" style="left:10px;top:2381px;width:315px;height:427px;border-radius:45% 45% 20% 20%;background:linear-gradient(180deg,#c98a5a 0%,#f3dcd0 45%,#f2b6c6 75%,#f7f0ec 100%)"></div>

<div class="abs cta-head">Lorem ipsum dolor sit tectetur piscing<br>elit, sed do eiusmods tempor ncididunt<br>aliquauspendisse ultrices gravida.</div>
<div class="btn" style="left:333px;top:2664px;width:324px;height:48px;font-size:16.5px">NEW FLORIST FRANCHISE INQUIRY</div>
<div class="btn btn-outline" style="left:682px;top:2663px;width:406px;height:50px;font-size:16.5px">PROFESSIONAL FLORIST FRANCHISE INQUIRY</div>

<!-- FOOTER -->
<div class="abs" style="left:0;top:2860px;width:1200px;height:376px;background:var(--mint)"></div>

<div class="abs brand" style="left:110px;top:2930px">
  <span class="brand-dot"></span><span>Lantern Petals</span>
</div>

<div class="abs script foot-title" style="left:494px;top:2892px">Quick Links</div>
<div class="abs foot-link" style="left:494px;top:2950px">Home</div>
<div class="abs foot-link" style="left:494px;top:2995px">About Us</div>
<div class="abs foot-link" style="left:494px;top:3039px">For Supermarkets</div>
<div class="abs foot-link" style="left:494px;top:3084px">For Franchisees</div>
<div class="abs foot-link" style="left:494px;top:3128px">Contact Us</div>

<div class="abs script foot-title" style="left:741px;top:2892px">Contact Us</div>

<div class="abs contact-row" style="left:738px;top:2944px">
  <div class="c-icon"><svg width="20" height="20" viewBox="0 0 24 24"><path fill="#fff" d="M3 5h18c.6 0 1 .4 1 1v1l-10 6L2 7V6c0-.6.4-1 1-1zm-1 4.3 10 6 10-6V18c0 .6-.4 1-1 1H3c-.6 0-1-.4-1-1z"/></svg></div>
  <div><div class="c-label">Email:</div><div class="c-val">mara@lanternpetals.com</div></div>
</div>
<div class="abs contact-row" style="left:738px;top:3026px">
  <div class="c-icon"><svg width="20" height="20" viewBox="0 0 24 24"><path fill="#fff" d="M6.6 10.8a15 15 0 0 0 6.6 6.6l2.2-2.2c.3-.3.7-.4 1-.2 1.1.4 2.3.6 3.6.6.6 0 1 .4 1 1V20c0 .6-.4 1-1 1A17 17 0 0 1 3 4c0-.6.4-1 1-1h3.5c.6 0 1 .4 1 1 0 1.3.2 2.5.6 3.6.1.3 0 .7-.2 1z"/></svg></div>
  <div><div class="c-label">Phone No:</div><div class="c-val">+1 555 204 7781</div></div>
</div>
<div class="abs contact-row" style="left:738px;top:3101px">
  <div class="c-icon"><svg width="20" height="20" viewBox="0 0 24 24"><path fill="#fff" d="M12 2a7 7 0 0 0-7 7c0 5 7 13 7 13s7-8 7-13a7 7 0 0 0-7-7zm0 9.5A2.5 2.5 0 1 1 12 6.5a2.5 2.5 0 0 1 0 5z"/></svg></div>
  <div><div class="c-label">Location:</div><div class="c-val">Lorem ipsum dolor sit amet,USA</div></div>
</div>

<div class="abs copyright">Copyright © 2024 Lantern Petals | All Rights Reserved</div>

</body>
</html>
```